Private practice for psychiatry and psychotherapy needs a business card and logo

I need a logo and business card design for my private practice for psychiatry and psychotherapy. The optional names for my practice are: Vorsteling Praktijk voor Psychiatrie en Psychotherapie, or short: Praktijk Vorsteling.
I am a (child and adolescent) psychiatrist and psychotherapist. I diagnose and treat infants, children, adolescents and adults with psychiatric symptoms/disorders. I also give supervision to colleagues about their own treatments. My work is characterised by personal involvement, transparence, creativity and professionality.
I would like to have an appealing, light and bright, yet basic design that invites people (both children and adults) to contact me, gives trust and hope, without loosing professional appearance.
I uploaded my contact information which should not necessarily be all included (in this form) on the card as long as people know how to contact me. Please feel free to be creative!
Please note that my website is only temporarely and need a new design and update too!

Target Market(s)

Clients and patients (children, adolescents, adults) with psychiatric symptoms who need diagnosis and treatment. I work with private clients and patients through medical insurances.

Industry/Entity Type

Mental Health

Contact Information for Business Card

Dr. Ilse Vorsteling-ter Haaf
Psychiater/Kinder- en Jeugdpsychiater
Jorisvan Heultstraat 14
3071 PW Rotterdam
t: 06-58190274
e: info@praktijkvorsteling.nl
i: www.praktijkvorsteling.nl

Logo Text

Praktijk Vorsteling voor Psychiatrie en Psychotherapie; or short: Praktijk Vorsteling

Font styles to use
Sans Serif
Other font styles liked:
• up to designer

Requirements
Must have
• Appealing, light, bright, creative, trustful, professional and unique.

```html
<!DOCTYPE html>
<html lang="nl">
<head>
<meta charset="utf-8">
<title>Praktijk Vorsteling – visitekaartje</title>
<link href="https://fonts.googleapis.com/css2?family=PT+Sans:wght@400;700&display=swap" rel="stylesheet">
<style>
  :root {
    --bg: #d9d9d9;
    --card: #f4f4f3;
    --blue: #1f63ad;
    --blue-soft: #4a7fc0;
    --red: #d42a5a;
    --ink: #1c1c1c;
    --shadow: rgba(0, 0, 0, 0.14);
  }
  * { box-sizing: border-box; margin: 0; padding: 0; }
  html, body {
    width: 1200px;
    height: 900px;
    overflow: hidden;
    background: var(--bg);
    font-family: "PT Sans", sans-serif;
  }
  .canvas {
    position: relative;
    width: 1200px;
    height: 900px;
  }
  .card {
    position: absolute;
    width: 560px;
    height: 330px;
    background: var(--card);
    box-shadow: 0 6px 18px var(--shadow);
  }

  /* Contact side */
  .card--contact { left: 110px; top: 80px; }
  .practice-title {
    position: absolute;
    left: 36px;
    top: 34px;
    display: flex;
    align-items: flex-start;
    gap: 12px;
  }
  .practice-title__square {
    width: 44px;
    height: 32px;
    background: var(--red);
    flex: none;
  }
  .practice-title__text {
    color: var(--blue);
    font-weight: 700;
    font-size: 17px;
    line-height: 1.1;
    text-transform: uppercase;
    letter-spacing: 0.3px;
  }
  .person {
    position: absolute;
    left: 36px;
    top: 138px;
    color: var(--ink);
    font-size: 15px;
    line-height: 1.2;
  }
  .person__name {
    color: var(--blue);
    font-weight: 700;
    font-size: 13px;
    text-transform: uppercase;
    letter-spacing: 0.3px;
    margin-bottom: 2px;
  }
  .contact {
    position: absolute;
    right: 36px;
    bottom: 34px;
    text-align: right;
    color: var(--ink);
    font-size: 15px;
    line-height: 1.2;
  }

  /* Logo side */
  .card--logo { left: 530px; top: 490px; }
  .brand {
    position: absolute;
    left: 70px;
    top: 110px;
    display: flex;
    align-items: center;
    gap: 22px;
  }
  .brand__dot {
    width: 90px;
    height: 90px;
    border-radius: 50%;
    background: var(--red);
    flex: none;
  }
  .brand__name {
    color: var(--ink);
    font-weight: 400;
    text-transform: uppercase;
    line-height: 1.05;
  }
  .brand__name-main { display: block; font-size: 30px; letter-spacing: 0.5px; }
  .brand__name-sub { display: block; font-size: 14.5px; letter-spacing: 0.4px; }
</style>
</head>
<body>
<main class="canvas">
  <section class="card card--contact" aria-label="Visitekaartje, contactzijde">
    <div class="practice-title">
      <span class="practice-title__square"></span>
      <h1 class="practice-title__text">Praktijk voor psychiatrie<br>en psychotherapie Vorsteling</h1>
    </div>
    <div class="person">
      <p class="person__name">Dr. Ilse Vorsteling-ter Haaf</p>
      <p>Psychiater/kinder- en jeugdpsychiater</p>
      <p>Jorisvan Heultstraat 14</p>
      <p>3071 PW&nbsp; Rotterdam</p>
    </div>
    <div class="contact">
      <p>06-58190274</p>
      <p>info@praktijkvorsteling.nl</p>
      <p>www.praktijkvorsteling.nl</p>
    </div>
  </section>

  <section class="card card--logo" aria-label="Visitekaartje, logozijde">
    <div class="brand">
      <span class="brand__dot"></span>
      <h2 class="brand__name">
        <span class="brand__name-main">Praktijk Vorsteling</span>
        <span class="brand__name-sub">voor psychiatrie en psychotherapie</span>
      </h2>
    </div>
  </section>
</main>
</body>
</html>
```